Nutrition company needs beverage package design (velno quadra 330)*

Company VitaCrest Pantry is a nutrition company seeking a dynamic package design of our upcoming Chocolate Lumo Diet Shake.Target audience Weight Loss consumers between the ages of 20 and 65. Our clients are health conscious and goal oriented in their approach to losing weight. Our customer base leans female.Color PreferencesThe packaging scheme must work with our logo (any color, solid or reversed) and be adaptable to various flavor options in the near future (vanilla, strawberry).The cap must be black, red or white.Look and FeelThe design should feel modern, upscale and reflect the gourmet quality of our product (taste). It must stand out on the shelf and present "LUMO SHAKE" as the primary focus of the design, with the words "naturally delicious" above it. (this text might change but some adjective will be in the spot regardless)We want to take it to the next level to ensure our packaging has character and drives sampling (makes you want to try it). Thanks - Looking forward to seeing your design(s)!Attached: best in-house effort to get the process and direction started, current co. logo (including white with transparent background) and velno box template if needed

```html
<!DOCTYPE html>
<html lang="en">
<head>
<meta charset="utf-8">
<title>VitaCrest Pantry – Lumo Shake Carton Front</title>
<link rel="stylesheet" href="https://fonts.googleapis.com/css2?family=Montserrat:wght@300;500;600;700;800&family=Oswald:wght@600&display=swap">
<style>
  :root {
    --canvas: #ffffff;
    --brand-red: #b5121b;
    --brand-red-dark: #8e0c14;
    --panel-white: #f4f4f4;
    --panel-shade: #dcdcdc;
    --cocoa: #5a3324;
    --cocoa-dark: #3a1e14;
    --cocoa-light: #7b4a35;
    --ink-brown: #5b4038;
    --ink-grey: #6d5f5a;
    --accent-gold: #c9a77a;
  }
  html, body {
    margin: 0;
    padding: 0;
    width: 1200px;
    height: 1000px;
    overflow: hidden;
    background: var(--canvas);
  }
  .canvas {
    position: relative;
    width: 1200px;
    height: 1000px;
  }
  .carton-front {
    position: absolute;
    left: 470px;
    top: 190px;
    width: 260px;
    height: 640px;
  }
  .brand-name {
    font-family: "Montserrat", sans-serif;
    font-weight: 700;
    fill: #ffffff;
  }
  .tagline {
    font-family: "Montserrat", sans-serif;
    font-weight: 500;
    fill: var(--ink-grey);
  }
  .title-primary {
    font-family: "Montserrat", sans-serif;
    font-weight: 800;
    fill: var(--brand-red);
  }
  .title-secondary {
    font-family: "Montserrat", sans-serif;
    font-weight: 300;
    fill: var(--ink-brown);
  }
  .benefit {
    font-family: "Montserrat", sans-serif;
    font-weight: 700;
    fill: var(--ink-grey);
  }
  .flavor-name, .volume {
    font-family: "Oswald", sans-serif;
    font-weight: 600;
    fill: #ffffff;
  }
</style>
</head>
<body>
<main class="canvas">
  <svg class="carton-front" viewBox="0 0 260 640" xmlns="http://www.w3.org/2000/svg" aria-label="Lumo Shake carton front panel">
    <defs>
      <linearGradient id="panelWhite" x1="0" y1="0" x2="1" y2="0">
        <stop offset="0" stop-color="#e6e6e6"/>
        <stop offset="0.25" stop-color="#fafafa"/>
        <stop offset="0.75" stop-color="#f6f6f6"/>
        <stop offset="1" stop-color="#dedede"/>
      </linearGradient>
      <linearGradient id="redTop" x1="0" y1="0" x2="1" y2="0">
        <stop offset="0" stop-color="#9a0d15"/>
        <stop offset="0.45" stop-color="#c4131d"/>
        <stop offset="1" stop-color="#900b13"/>
      </linearGradient>
      <linearGradient id="cocoaFill" x1="0" y1="0" x2="0" y2="1">
        <stop offset="0" stop-color="#6e412d"/>
        <stop offset="1" stop-color="#3a1e14"/>
      </linearGradient>
    </defs>

    <rect class="panel-body" x="0" y="0" width="260" height="640" fill="url(#panelWhite)"/>

    <path class="top-shade" d="M0 142 Q130 175 260 228 L260 250 Q130 195 0 158 Z" fill="var(--panel-shade)" opacity="0.7"/>

    <path class="top-band" d="M0 0 H260 V222 Q130 160 0 138 Z" fill="url(#redTop)"/>

    <g class="brand">
      <circle cx="130" cy="112" r="11" fill="none" stroke="#ffffff" stroke-width="2"/>
      <text class="brand-name" x="130" y="140" font-size="11" text-anchor="middle" letter-spacing="0.6">VITACREST PANTRY</text>
    </g>

    <g class="tagline-group">
      <line x1="28" y1="239" x2="36" y2="239" stroke="var(--accent-gold)" stroke-width="1.4"/>
      <text class="tagline" x="130" y="243" font-size="10.5" text-anchor="middle" letter-spacing="1.6">NATURALLY DELICIOUS</text>
      <line x1="224" y1="239" x2="232" y2="239" stroke="var(--accent-gold)" stroke-width="1.4"/>
    </g>

    <text class="title-primary" x="130" y="309" font-size="68" text-anchor="middle" letter-spacing="-1">LUMO</text>
    <rect class="title-bar" x="0" y="314" width="17" height="45" fill="var(--brand-red)"/>
    <rect class="title-bar" x="228" y="314" width="32" height="45" fill="var(--brand-red)"/>
    <text class="title-secondary" x="123" y="358" font-size="52" text-anchor="middle" letter-spacing="-0.5">SHAKE</text>

    <g class="benefits" font-size="8.6">
      <circle cx="26" cy="415" r="1.3" fill="var(--accent-gold)"/>
      <text class="benefit" x="31" y="418">PREMIUM MCTS</text>
      <circle cx="26" cy="432" r="1.3" fill="var(--accent-gold)"/>
      <text class="benefit" x="31" y="435">SUGAR FREE</text>
      <circle cx="26" cy="449" r="1.3" fill="var(--accent-gold)"/>
      <text class="benefit" x="31" y="452">LOW CARB</text>
      <circle cx="26" cy="466" r="1.3" fill="var(--accent-gold)"/>
      <text class="benefit" x="31" y="469">GLUTEN FREE</text>
    </g>

    <g class="chocolate-art" role="img" aria-label="Chocolate shake pouring with chocolate chunks and a splash">
      <path d="M260 285 L260 325 L196 540 L170 540 Z" fill="url(#cocoaFill)"/>
      <path d="M0 596 L260 498 V640 H0 Z" fill="url(#cocoaFill)"/>
    </g>

    <path class="flavor-band" d="M0 552 L260 457 V500 L0 598 Z" fill="var(--brand-red)"/>
    <text class="flavor-name" x="0" y="0" font-size="13" letter-spacing="0.3"
          transform="translate(48 571) rotate(-20)">CHOCOLATE TRUFFLE</text>

    <text class="volume" x="178" y="631" font-size="9" text-anchor="middle">11.1 FL OZ (330 ML)</text>
  </svg>
</main>
</body>
</html>
```